Visitenkarten-Design für App Start Up
Zielgruppe
Wir sind ein Start-Up und haben unsere Tormeko App gerelauncht.
Wir haben zwei Zielgruppen für unsere App. Zum einen lokale Gewerbetreibende, welche in Echtzeit Angebote (Coupons) erstellen können und zum anderen private User, welche diese innerhalb eines vorgegebenen Zeitraumes reservieren und einlösen können.
Hierfür müssen wir auch unsere Visitenkarten auf unser neues Design anpassen.
Aufgabenstellung
Visitenkarten sollten beidseitig bedruckt sein und auf der Vorderseite sollte unser Tormeko Logo und/oder der App Name Tormeko versehen sein. Auf der Rückseite benötigen wir die Infos: Name, Position, Firma inkl. Anschrift, E-Mail sowie die Telefonnummer.
Ansonsten freuen wir uns auf weitere kreative Ansätze.

```html
<!DOCTYPE html>
<html lang="de">
<head>
<meta charset="utf-8">
<title>Tormeko Visitenkarten</title>
<link href="https://fonts.googleapis.com/css2?family=Poppins:wght@400;500;600&display=swap" rel="stylesheet">
<style>
  :root {
    --backdrop: #1fae98;
    --card: #ffffff;
    --ink: #2e3137;
    --ink-soft: #4a4d54;
    --magenta: #c63a86;
    --blue: #0d8fcb;
  }
  * { margin: 0; padding: 0; box-sizing: border-box; }
  html, body {
    width: 1200px; height: 849px; overflow: hidden;
    background: var(--backdrop);
    font-family: "Poppins", sans-serif;
  }
  .canvas { position: relative; width: 1200px; height: 849px; }
  .card { position: absolute; background: var(--card); }

  .card-front { left: 118px; top: 278px; width: 438px; height: 283px; }
  .front-mark {
    position: absolute; left: 50%; top: 78px; transform: translateX(-50%);
    width: 64px; height: 64px; border-radius: 50%; background: var(--magenta);
  }
  .front-name {
    position: absolute; left: 0; right: 0; top: 172px; text-align: center;
    font-weight: 500; font-size: 28px; letter-spacing: 0.12em; color: var(--ink);
  }

  .card-back { left: 686px; top: 213px; width: 283px; height: 437px; text-align: center; color: var(--ink-soft); }
  .back-mark {
    position: absolute; left: 50%; top: 62px; transform: translateX(-50%);
    width: 52px; height: 52px; border-radius: 50%; background: var(--magenta);
  }
  .back-brand {
    position: absolute; left: 0; right: 0; top: 124px;
    font-weight: 500; font-size: 20px; letter-spacing: 0.12em; color: var(--ink);
  }
  .person-name { position: absolute; left: 0; right: 0; top: 205px; font-weight: 600; font-size: 18.5px; color: var(--ink); }
  .person-role { position: absolute; left: 0; right: 0; top: 228px; font-size: 13.5px; }
  .company { position: absolute; left: 0; right: 0; top: 269px; font-size: 12px; line-height: 14.6px; }
  .contacts { position: absolute; left: 74px; top: 338px; list-style: none; text-align: left; font-size: 12.5px; }
  .contacts li { display: flex; align-items: center; height: 22px; }
  .contacts svg { width: 14px; height: 14px; margin-right: 11px; flex: none; }
</style>
</head>
<body>
<main class="canvas">
  <section class="card card-front" aria-label="Vorderseite">
    <div class="front-mark"></div>
    <div class="front-name">TORMEKO</div>
  </section>

  <section class="card card-back" aria-label="Rückseite">
    <div class="back-mark"></div>
    <div class="back-brand">TORMEKO</div>
    <div class="person-name">Lena Beispiel</div>
    <div class="person-role">Geschäftsführer</div>
    <div class="company">TORMEKO GmbH<br>Beispielweg 7<br>54321 Beispielstadt</div>
    <ul class="contacts">
      <li>
        <svg viewBox="0 0 16 16" fill="none" stroke="var(--magenta)" stroke-width="1.4" stroke-linejoin="round">
          <path d="M3 1.5l2.5 0 1.2 3-1.6 1.2c.8 1.8 2.2 3.2 4 4l1.2-1.6 3 1.2v2.5c0 .8-.7 1.5-1.5 1.5C6.5 13.3 2.7 9.5 1.5 4.5 1.5 2.2 2.2 1.5 3 1.5z"/>
        </svg>01234/ 567890
      </li>
      <li>
        <svg viewBox="0 0 16 16" fill="none" stroke="var(--magenta)" stroke-width="1.4" stroke-linejoin="round">
          <rect x="1" y="3" width="14" height="10"/><path d="M4 6l4 3 4-3"/>
        </svg>mail@tormeko.de
      </li>
      <li>
        <svg viewBox="0 0 16 16" fill="none" stroke="var(--blue)" stroke-width="1.3">
          <circle cx="8" cy="8" r="6.5"/><ellipse cx="8" cy="8" rx="2.8" ry="6.5"/><path d="M1.5 8h13"/>
        </svg>www.tormeko.de/info
      </li>
    </ul>
  </section>
</main>
</body>
</html>
```